A layout of a webpage for oil trade platform

I would like to have a desgin of one page webpage (with section scrollling dowin) that woulf present the new product i.e. oil trade platform for wholesale buyers and sellers.
Layout should consist of the sections similar to the given at: https://porada.leczmypol.pl/panel-planowania-spotkan
However oil industy require more colors and more photo stories than here for doctor.
I. I woul imagine at first below menu a slider with brueg information about the product and its advantages with "more" button next to the prict screen of our platform on different displays (PC and mobile).
II. Bellow the slider I would imagine icons correspoing to the advantages of that plaftorm:
1. Purchase/sale process automation 24/7
2. Access to the best deals
3. Electronic offerings and orderings
4. Transaction status monitoring
5. Data and transaction security
II A) (optional):
In near future we would like to prepare a short video presenation. Hence please prepare a place to display that element here.
At the moment alternatvily please prepare a How it works section that would explan the platform operating process
III. Next secion is about benefits for Oil Purchaser
It can be done either by icons of by text and corresponding grahip for while section.
Benefits:
- Access to cheaper oil
- Convenience of online orders
- Possibility to compare prices on the market
- Transaction history
- Order status monitoring
- Seccurity and transparency of purchase
IV. Next seciont is about benefits for Oil Seller
Benefits:
- New sale channel
- Attracting new clients
- More oil sold
- Transaction security
- Possibility to integrate with distribution infrastructure and logistits for more efficient automation.
V. Contact form
VI. Footer
I would need a layout that that will correspond to the very dynamic logo but I would expect also a clean form, smoth and modern. It has to be proffessional layout with more corporate character.
It can use a paralax features if needed.

```html
<!DOCTYPE html>
<html lang="en">
<head>
<meta charset="utf-8">
<title>Oleovia — Oil Trade Platform</title>
<link rel="stylesheet" href="https://fonts.googleapis.com/css2?family=Montserrat:wght@400;600;700&family=Questrial&display=swap">
<style>
:root{
  --orange:#f26522;
  --navy:#0f1f3d;
  --band:#3b4a68;
  --footer:#2f3b57;
  --ink:#333a45;
  --muted:#8a8f98;
  --light:#f4f4f4;
  --line:#cfd3d8;
  --teal:#3fb8af;
  --green:#7cb342;
  --salmon:#e2685f;
  --white:#ffffff;
  --device:#14171d;
  --screen:#e9edf2;
}
*{box-sizing:border-box;margin:0;padding:0}
html,body{width:1200px;height:3309px;overflow:hidden}
body{font-family:"Questrial",sans-serif;color:var(--ink);background:var(--white)}
.wrap{width:1000px;margin:0 auto;position:relative}

/* header */
.site-header{height:118px;display:flex;align-items:center;justify-content:space-between;padding:0 100px}
.brand{display:flex;align-items:center;gap:12px;font-family:"Montserrat",sans-serif;font-weight:700;font-size:30px;color:var(--navy);text-decoration:none}
.brand-dot{width:34px;height:34px;border-radius:50%;background:var(--orange)}
.main-nav{display:flex;gap:40px;font-family:"Montserrat",sans-serif;font-size:14px;color:#555}
.main-nav a{color:inherit;text-decoration:none}
.main-nav a.active{color:#111;font-weight:600}

/* hero */
.hero{height:583px;position:relative;background:linear-gradient(100deg,#4a5468 0%,#6b7385 45%,#3c4558 100%);overflow:hidden}
.hero-copy{position:absolute;left:100px;top:150px;width:440px;color:var(--white);z-index:2}
.hero-title{font-family:"Montserrat",sans-serif;font-weight:700;font-size:48px;letter-spacing:1px;line-height:56px}
.hero-text{font-size:17px;line-height:27px;margin-top:14px;color:#e8eaee}
.btn-orange{display:inline-block;margin-top:36px;width:167px;height:47px;line-height:47px;text-align:center;background:var(--orange);color:var(--white);font-family:"Montserrat",sans-serif;font-weight:600;font-size:17px;border-radius:3px}
.slider-arrows{position:absolute;left:100px;top:396px;display:flex;gap:10px}
.slider-arrows span{width:34px;height:34px;border-radius:50%;background:rgba(20,25,35,.75);display:flex;align-items:center;justify-content:center}
.devices{position:absolute;left:400px;top:0;width:800px;height:583px}

/* features */
.features{height:334px;display:flex;justify-content:space-between;padding:120px 90px 0}
.feature{width:200px;text-align:center;font-size:14px;color:var(--muted);line-height:18px}
.feature svg{display:block;margin:0 auto 20px}

/* video */
.video-section{height:530px;background:var(--light);padding-top:70px}
.section-title{font-family:"Questrial",sans-serif;font-size:32px;text-align:center;letter-spacing:1px;color:#333;font-weight:400}
.video-row{display:flex;justify-content:space-between;margin-top:45px}
.video-copy{width:540px;font-size:15px;line-height:26px;color:var(--muted)}
.video-copy p+p{margin-top:14px}
.btn-navy{display:inline-flex;align-items:center;gap:12px;margin-top:38px;height:48px;padding:0 22px;background:var(--navy);color:var(--white);font-family:"Montserrat",sans-serif;font-size:16px;letter-spacing:.5px}
.video-frame{width:435px;height:282px;border:1px solid var(--line);background:var(--white);padding:10px}
.video-screen{width:100%;height:100%;position:relative;background:linear-gradient(180deg,#4e6a86 0%,#9fb0bf 55%,#2d3b4c 100%)}
.video-play{position:absolute;left:50%;top:42%;transform:translate(-50%,-50%)}
.video-bar{position:absolute;left:0;right:0;bottom:0;height:30px;background:#1b1f26;display:flex;align-items:center;gap:12px;padding:0 10px}
.video-track{flex:1;height:5px;background:#777;border-radius:3px;position:relative}
.video-track i{position:absolute;left:0;top:0;bottom:0;width:40%;background:#4a90d9;border-radius:3px}

/* purchaser */
.purchaser{height:463px;background:var(--band);color:var(--white);padding-top:70px;text-align:center}
.purchaser .section-title{color:var(--white)}
.section-desc{width:860px;margin:22px auto 0;font-size:13px;line-height:20px}
.purchaser .section-desc{color:#d5dae4}
.benefit-row{display:flex;justify-content:space-between;margin:50px 100px 0}
.benefit{width:140px;font-size:14px;line-height:17px}
.benefit .ring{width:115px;height:115px;border-radius:50%;border:2px solid rgba(255,255,255,.25);margin:0 auto 16px;display:flex;align-items:center;justify-content:center}

/* seller */
.seller{height:454px;background:var(--light);padding-top:70px;text-align:center}
.seller .section-desc{color:#666}
.seller-row{display:flex;justify-content:space-between;align-items:flex-start;margin:60px 90px 0}
.seller-item{width:200px;font-size:14px;color:var(--muted);line-height:17px}
.seller-item svg{display:block;margin:0 auto 20px}

/* contact */
.contact{height:493px;padding-top:56px;text-align:center}
.contact .section-desc{color:#666;font-size:15px;line-height:22px;width:500px;margin-top:14px}
.form-grid{display:grid;grid-template-columns:repeat(4,1fr);gap:20px;width:1000px;margin:40px auto 0}
.field{height:43px;border:1px solid var(--line);font-size:13px;color:#999;text-align:left;padding:12px 16px}
.field-message{grid-column:1/5;height:75px}
.btn-submit{display:inline-block;margin-top:33px;width:208px;height:53px;line-height:53px;border:1px solid #999;font-family:"Montserrat",sans-serif;font-size:17px;letter-spacing:1px;color:#333}

/* footer */
.site-footer{height:334px;background:var(--footer);color:var(--white);position:relative}
.footer-brand{position:absolute;left:100px;top:105px;display:flex;align-items:center;gap:14px;font-family:"Montserrat",sans-serif;font-weight:700;font-size:36px}
.footer-brand .brand-dot{width:44px;height:44px}
.footer-col{position:absolute;top:52px;height:198px;border-left:1px solid rgba(255,255,255,.12)}
.footer-col h4{font-family:"Questrial",sans-serif;font-weight:400;font-size:16px;letter-spacing:1px;margin:0 0 20px 0}
.footer-col ul{list-style:none;font-size:14px;line-height:30px;color:#d5dae4}
.col-links{left:490px;padding-left:22px}
.col-touch{left:665px;padding-left:22px}
.col-follow{left:905px;padding-left:22px}
.footer-col li{display:flex;align-items:center;gap:12px}
.socials{display:flex;gap:6px;margin-top:12px}
.socials span{width:34px;height:34px;border-radius:50%;background:#3f8fd6;border:2px solid var(--white)}
.socials span:nth-child(4){background:#dd4b39}
.footer-rule{position:absolute;left:100px;right:100px;top:260px;border-top:1px solid rgba(255,255,255,.25)}
.copyright{position:absolute;left:100px;top:282px;font-size:13px;color:#e0e4ea}
</style>
</head>
<body>

<header class="site-header">
  <a class="brand" href="#"><span class="brand-dot"></span>Oleovia</a>
  <nav class="main-nav">
    <a class="active" href="#">HOME</a><a href="#">ABOUT US</a><a href="#">OUR SERVICES</a><a href="#">BLOG</a><a href="#">OIL SELLER</a><a href="#">CONTACT US</a>
  </nav>
</header>

<section class="hero" role="img" aria-label="Industrial oil pipeline scene in dusky blue tones">
  <div class="hero-copy">
    <h1 class="hero-title">OIL TRADE</h1>
    <p class="hero-text">Excepteur sint occaecat cupidatat non proident, sunt in culpa qui officia deserunt mollit anim.</p>
    <span class="btn-orange">READ MORE</span>
  </div>
  <div class="slider-arrows">
    <span><svg width="12" height="12" viewBox="0 0 12 12"><path d="M8 1 3 6l5 5" fill="none" stroke="#fff" stroke-width="2"/></svg></span>
    <span><svg width="12" height="12" viewBox="0 0 12 12"><path d="M4 1l5 5-5 5" fill="none" stroke="#fff" stroke-width="2"/></svg></span>
  </div>
  <svg class="devices" viewBox="0 0 800 583" role="img" aria-label="Platform dashboard shown on desktop, laptop, tablet and phone screens">
    <!-- desktop monitor -->
    <rect x="170" y="136" width="560" height="320" rx="8" fill="var(--device)"/>
    <rect x="182" y="148" width="536" height="290" fill="var(--screen)"/>
    <rect x="182" y="148" width="110" height="290" fill="#2c3a52"/>
    <path d="M410 456h100l14 70H396z" fill="var(--device)"/>
    <rect x="370" y="524" width="180" height="10" rx="3" fill="var(--device)"/>
    <!-- laptop -->
    <rect x="8" y="367" width="325" height="200" rx="8" fill="var(--device)"/>
    <rect x="18" y="380" width="305" height="178" fill="var(--screen)"/>
    <rect x="18" y="380" width="60" height="178" fill="#2c3a52"/>
    <rect x="0" y="565" width="341" height="10" rx="3" fill="#0e1014"/>
    <!-- tablet -->
    <rect x="655" y="350" width="92" height="185" rx="8" fill="var(--device)"/>
    <rect x="662" y="365" width="78" height="155" fill="var(--screen)"/>
    <!-- phone -->
    <rect x="622" y="420" width="70" height="150" rx="8" fill="#0e1014"/>
    <rect x="628" y="434" width="58" height="120" fill="var(--screen)"/>
  </svg>
</section>

<section class="features">
  <div class="feature">
    <svg width="80" height="80" viewBox="0 0 80 80"><circle cx="40" cy="40" r="28" fill="none" stroke="#5aa64a" stroke-width="4"/><text x="40" y="48" text-anchor="middle" font-family="Montserrat,sans-serif" font-weight="700" font-size="20" fill="#5aa64a">24</text></svg>
    Purchase/sale process automation 24/7
  </div>
  <div class="feature">
    <svg width="80" height="80" viewBox="0 0 80 80"><g transform="rotate(-20 40 40)"><rect x="12" y="22" width="56" height="30" rx="3" fill="var(--teal)"/><rect x="16" y="30" width="56" height="30" rx="3" fill="#5fcbc2"/><circle cx="44" cy="45" r="8" fill="#fff"/></g></svg>
    Access to the best deals
  </div>
  <div class="feature">
    <svg width="80" height="80" viewBox="0 0 80 80"><rect x="8" y="18" width="46" height="32" rx="3" fill="none" stroke="var(--salmon)" stroke-width="4"/><path d="M24 58h14M31 50v8" stroke="var(--salmon)" stroke-width="4"/><rect x="50" y="30" width="22" height="32" rx="3" fill="#fff" stroke="var(--salmon)" stroke-width="4"/></svg>
    Electronic offerings and orderings
  </div>
  <div class="feature">
    <svg width="80" height="80" viewBox="0 0 80 80"><g fill="none" stroke="#5aa6a0" stroke-width="3"><rect x="12" y="46" width="9" height="16"/><rect x="25" y="38" width="9" height="24"/><rect x="38" y="30" width="9" height="32"/><rect x="51" y="22" width="9" height="40"/><path d="M10 44 30 30l14 6 22-20"/></g><path d="M60 14h8v8" fill="none" stroke="#5aa6a0" stroke-width="3"/></svg>
    Transaction status monitoring
  </div>
  <div class="feature">
    <svg width="80" height="80" viewBox="0 0 80 80"><g fill="none" stroke="var(--orange)" stroke-width="3"><rect x="10" y="12" width="40" height="12"/><rect x="10" y="28" width="40" height="12"/><rect x="10" y="44" width="40" height="12"/><circle cx="52" cy="52" r="10" fill="#fff"/><path d="M59 59l10 10"/></g></svg>
    Data and transaction security
  </div>
</section>

<section class="video-section">
  <h2 class="section-title">OUR VIDEO</h2>
  <div class="wrap video-row">
    <div class="video-copy">
      <p>Sed ut perspiciatis unde omnis iste natus error sit voluptatem accusantium doloremque laudantium, totam rem aperiam, eaque ipsa quae ab illo inventore veritatis et quasi architecto beatae vitae dicta sunt explicabo.</p>
      <p>Ut enim ad minim veniam, quis nostrud exercitation ullamco laboris nisi ut aliquip ex ea commodo consequat. Duis aute irure dolor in reprehenderit in voluptate velit esse cillum dolore eu fugiat nulla pariatur. Excepteur sint occaecat cupidatat non proident.</p>
      <span class="btn-navy">MORE INFORMATION <svg width="10" height="12" viewBox="0 0 10 12"><path d="M2 1l5 5-5 5" fill="none" stroke="#fff" stroke-width="2"/></svg></span>
    </div>
    <div class="video-frame">
      <div class="video-screen" role="img" aria-label="Offshore oil platform at sunset over the sea">
        <svg class="video-play" width="76" height="76" viewBox="0 0 76 76"><circle cx="38" cy="38" r="34" fill="rgba(0,0,0,.25)" stroke="#fff" stroke-width="4"/><path d="M30 24v28l22-14z" fill="#fff"/></svg>
        <div class="video-bar">
          <svg width="12" height="14" viewBox="0 0 12 14"><path d="M1 1v12l10-6z" fill="#fff"/></svg>
          <div class="video-track"><i></i></div>
          <svg width="16" height="14" viewBox="0 0 16 14"><path d="M1 5h4l4-4v12L5 9H1z" fill="#fff"/><path d="M11 4q3 3 0 6" fill="none" stroke="#fff" stroke-width="1.5"/></svg>
        </div>
      </div>
    </div>
  </div>
</section>

<section class="purchaser">
  <h2 class="section-title">BENEFITS FOR OIL PURCHASER</h2>
  <p class="section-desc">Sed ut perspiciatis unde omnis iste natus error sit voluptatem accusantium doloremque laudantium, totam rem aperiam, eaque ipsa quae ab illo inventore veritatis et quasi architecto beatae vitae dicta sunt explicabo.</p>
  <div class="benefit-row">
    <div class="benefit"><div class="ring"><svg width="60" height="40" viewBox="0 0 60 40"><path d="M6 16h30l10-6 8 4-10 6v12H10z" fill="#c5d233"/><path d="M50 24q2 5 0 8" stroke="#c5d233" stroke-width="3" fill="none"/></svg></div>Access to cheaper oil</div>
    <div class="benefit"><div class="ring"><svg width="54" height="46" viewBox="0 0 54 46"><rect x="4" y="4" width="46" height="30" fill="none" stroke="var(--teal)" stroke-width="4"/><path d="M16 18l8 8 14-14M20 42h14" fill="none" stroke="var(--teal)" stroke-width="4"/></svg></div>Convenience of online orders</div>
    <div class="benefit"><div class="ring"><svg width="50" height="50" viewBox="0 0 50 50"><path d="M26 4h18v18L22 44 4 26z" fill="none" stroke="var(--salmon)" stroke-width="4"/><circle cx="36" cy="13" r="3" fill="var(--salmon)"/></svg></div>Possibility to compare prices on the market</div>
    <div class="benefit"><div class="ring"><svg width="60" height="44" viewBox="0 0 96 70"><path d="M2 20 16 14 26 40 12 46z M94 20 80 14 70 40 84 46z" fill="#5aa6a0"/><path d="M18 20 40 13l16 8 22-6-6 26-14 11q-6 4-12 0L24 42z" fill="#5aa6a0"/><path d="M38 34l8 8M44 30l8 8M50 26l8 8M40 13l-8 14q4 4 10 0l8-8" fill="none" stroke="var(--band)" stroke-width="3"/></svg></div>Transaction history</div>
    <div class="benefit"><div class="ring"><svg width="50" height="46" viewBox="0 0 50 46"><rect x="4" y="4" width="42" height="30" fill="none" stroke="var(--orange)" stroke-width="4"/><path d="M14 26v-6M21 26v-10M28 26v-8M35 26v-12M18 42h14" stroke="var(--orange)" stroke-width="4"/></svg></div>Order status monitoring</div>
    <div class="benefit"><div class="ring"><svg width="40" height="50" viewBox="0 0 40 50"><path d="M10 22v-8a10 10 0 0 1 20 0v8" fill="none" stroke="var(--green)" stroke-width="4"/><rect x="4" y="22" width="32" height="26" rx="2" fill="var(--green)"/></svg></div>Security and transparency of purchase</div>
  </div>
</section>

<section class="seller">
  <h2 class="section-title">BENEFITS FOR OIL SELLER</h2>
  <p class="section-desc">At vero eos et accusamus et iusto odio dignissimos ducimus qui blanditiis praesentium voluptatum deleniti atque corrupti quos dolores et quas molestias excepturi sint occaecati cupiditate non provident</p>
  <div class="seller-row">
    <div class="seller-item"><svg width="96" height="90" viewBox="0 0 96 70"><path d="M2 20 16 14 26 40 12 46z M94 20 80 14 70 40 84 46z" fill="#3e8d90"/><path d="M18 20 40 13l16 8 22-6-6 26-14 11q-6 4-12 0L24 42z" fill="#3e8d90"/><path d="M38 34l8 8M44 30l8 8M50 26l8 8M40 13l-8 14q4 4 10 0l8-8" fill="none" stroke="var(--light)" stroke-width="3"/></svg>New sale channel</div>
    <div class="seller-item"><svg width="96" height="90" viewBox="0 0 96 70"><g fill="var(--green)"><circle cx="48" cy="18" r="12"/><path d="M28 60q0-26 20-26t20 26z"/><circle cx="22" cy="26" r="9"/><path d="M6 60q0-20 16-20 6 0 8 3-4 7-4 17z"/><circle cx="74" cy="26" r="9"/><path d="M90 60q0-20-16-20-6 0-8 3 4 7 4 17z"/></g></svg>Attracting new clients</div>
    <div class="seller-item"><svg width="96" height="90" viewBox="0 0 96 90"><g fill="none" stroke="var(--salmon)" stroke-width="4" stroke-linejoin="round"><path d="M8 86h80"/><path d="M38 86 52 36 66 86"/><path d="M18 28 84 42"/><path d="M18 18q-10 10-2 24"/><path d="M12 40v38"/><path d="M82 42l-6 24"/><circle cx="76" cy="66" r="8"/><path d="M76 74v12"/></g><rect x="5" y="76" width="14" height="10" fill="var(--salmon)"/><circle cx="52" cy="35" r="4" fill="var(--salmon)"/></svg>More oil sold</div>
    <div class="seller-item"><svg width="96" height="90" viewBox="0 0 96 80"><path d="M48 4l32 10v24q0 24-32 38-32-14-32-38V14z" fill="#5a9b6f"/><path d="M34 40l10 10 18-20" fill="none" stroke="#fff" stroke-width="6"/></svg>Transaction security</div>
    <div class="seller-item"><svg width="96" height="90" viewBox="0 0 96 76"><g fill="var(--orange)"><circle cx="38" cy="34" r="18"/><circle cx="70" cy="54" r="12"/></g><g stroke="var(--orange)" stroke-width="6"><path d="M38 10v48M14 34h48M21 17l34 34M55 17 21 51"/><path d="M70 38v32M54 54h32"/></g><circle cx="38" cy="34" r="7" fill="var(--light)"/><circle cx="70" cy="54" r="5" fill="var(--light)"/></svg>Possibility to integrate with distribution infrastructure and logistics for more efficient automation</div>
  </div>
</section>

<section class="contact">
  <h2 class="section-title">CONTACT FORM</h2>
  <p class="section-desc">Nostrum exercitationem ullam corporis suscipit laboriosam, nisi ut aliquid ex ea commodi consequatur</p>
  <div class="form-grid">
    <div class="field">First name</div>
    <div class="field">Last name</div>
    <div class="field">Email address</div>
    <div class="field">Phone number</div>
    <div class="field field-message">Message</div>
  </div>
  <span class="btn-submit">SUBMIT NOW !</span>
</section>

<footer class="site-footer">
  <div class="footer-brand"><span class="brand-dot"></span>Oleovia</div>
  <div class="footer-col col-links">
    <h4>LINKS</h4>
    <ul><li>Customers</li><li>Team</li><li>FAQ</li><li>Contact</li></ul>
  </div>
  <div class="footer-col col-touch">
    <h4>GET IN TOUCH</h4>
    <ul>
      <li><svg width="14" height="14" viewBox="0 0 14 14"><path d="M3 1l3 3-2 2q1 3 4 4l2-2 3 3-2 2Q4 12 1 3z" fill="#fff"/></svg>Call us on 000-xxx-00</li>
      <li><svg width="14" height="12" viewBox="0 0 14 12"><rect x="1" y="1" width="12" height="10" fill="#fff"/><path d="M1 1l6 5 6-5" fill="none" stroke="var(--footer)" stroke-width="1.5"/></svg>m.hale@oleovia.com</li>
    </ul>
  </div>
  <div class="footer-col col-follow">
    <h4>FOLLOW US</h4>
    <ul><li>Please connect with us on</li></ul>
    <div class="socials"><span></span><span></span><span></span><span></span></div>
  </div>
  <div class="footer-rule"></div>
  <p class="copyright">© 2017 Oleovia.&nbsp; All right reserved.&nbsp; Term of Use</p>
</footer>

</body>
</html>
```